Morvane Capital, a private equity fund, needs a brochure

Morvane Capital is a private equity fund dedicated to the development of budget hotels in France (reasonably priced hotel rooms).
Our customers are French private and high-income investors.

The brochure should communicate :
- seriousness and expertise
- trust, confidence and security
- financial product and profitability

The title is : Investissez dans l'hôtellerie économique et l'immobilier

Brochure size :
3 pages A4
Open size : 63 x 29,7 cm
Closed size : 21 x 29,7 cm

Our competitors :
Trelisse http://trelisse-immo-horizon.example/
789 Parcours http://www.789parcours.example/
GLD Capital http://www.gldam.example/
Soltane capital http://www.soltanecapital.example/
Barostel http://www.barostel.example/

Target Market(s)

Private investors, high-income ; Institutional investors ; Target customers are French private investors with high revenue.

Industry/Entity Type

Financial

Requirements
Must have
• - Brochure must respect our identity (you can see our logo) and use its colors and typo (and/or same typo style)
- You must use pictures on each interior pages (pictures of projetc and hotels)

```html
<!DOCTYPE html>
<html lang="fr">
<head>
<meta charset="utf-8">
<title>Morvane Capital – Brochure</title>
<link href="https://fonts.googleapis.com/css2?family=Arimo:wght@400;700&family=Fira+Sans+Condensed:wght@600&display=swap" rel="stylesheet">
<style>
  :root{
    --ground:#e6e6e6;
    --paper:#ffffff;
    --ink:#222222;
    --red:#b01d22;
    --red-dark:#8c1519;
    --grey:#b9bbb9;
    --sky:#12a8e6;
    --blue:#0f6fb5;
    --navy:#0d3f66;
    --black:#1a1a1a;
    --rule:#bdbdbd;
  }
  *{box-sizing:border-box;margin:0;padding:0}
  html,body{width:900px;height:1200px;overflow:hidden;background:var(--ground)}
  body{font-family:"Arimo",Arial,sans-serif;color:var(--ink)}
  .page{position:absolute;left:62px;top:48px;width:776px;height:1108px;background:var(--paper)}
  .block{position:absolute;left:36px;width:460px;font-size:12.2px;line-height:15.5px}
  .section-title{font-family:"Fira Sans Condensed",Arial Narrow,sans-serif;font-weight:600;color:var(--red);font-size:14.5px;line-height:16px}
  .points{list-style:none;font-weight:700}
  .points li,.plain li{position:relative;padding-left:16px}
  .points li::before,.plain li::before{content:"";position:absolute;left:0;top:4px;width:8px;height:8px;background:var(--red)}
  .plain{list-style:none}
  .plain li{margin-bottom:15px}
  p{text-align:justify}
  .gain-chart{position:absolute;left:0;top:480px}
  .share-chart{position:absolute;left:508px;top:756px}
  .footer-rule{position:absolute;left:0;right:0;top:1042px;height:1px;background:var(--rule)}
</style>
</head>
<body>
<main class="page">
  <section class="block" style="top:80px">
    <h2 class="section-title">Immobilier, valeur refuge pour l’investisseur<br>(selon l’analyse de MORVANE CAPITAL)</h2>
    <ul class="points" style="margin-top:18px">
      <li>Un investissement dans la pierre.</li>
      <li>Une réponse à l’incertitude des marchés financiers et de la monnaie et des risques d’inflation..</li>
      <li>Des emplacements exceptionnels (centres villes, aéroports, zones commerciales).</li>
    </ul>
  </section>

  <section class="block" style="top:224px">
    <h2 class="section-title">Trois sources potentielles de gains:</h2>
    <p style="margin-top:14px">Une double plus-value potentielle hôtelière et immobilière assortie d’un rendement annuel. La création de valeur pour chacun des hôtels dans lesquels MORVANE CAPITAL prendra des participations proviendra de la valorisation des murs de l’hôtel, de la valorisation de son fonds de commerce et de la rentabilité annuelle de l’exploitation. L’activité de location de meublés de tourisme bénéficie des mêmes synergies.</p>
    <p style="margin-top:15px">La création de valeur pour l’activité de promotion immobilière (construction vente des immeubles) proviendra des marges dégagées par les opérations de promotion</p>
    <ul class="points" style="margin-top:16px">
      <li>Trois sources potentielles de gains, assorties toutefois d’un risque de perte en capital</li>
      <li>Atténuation de risques du fait de l’investissement diversifié dans les murs et dans le fonds de commerce</li>
      <li>Un recours à un financement peu couteux</li>
    </ul>
  </section>

  <svg class="gain-chart" width="776" height="230" viewBox="0 0 776 230" font-family="Arimo, Arial, sans-serif">
    <rect x="30" y="155" width="146" height="29" fill="var(--red-dark)"/>
    <polygon points="176,133 491,32 491,184 176,184" fill="var(--grey)"/>
    <g stroke="#fff" stroke-width="1.5">
      <line x1="239" y1="113" x2="239" y2="184"/><line x1="302" y1="93" x2="302" y2="184"/>
      <line x1="365" y1="72" x2="365" y2="184"/><line x1="428" y1="52" x2="428" y2="184"/>
      <line x1="113" y1="155" x2="113" y2="184"/>
    </g>
    <polyline points="50,176 113,155 176,133 239,114 302,93 365,72 428,52 491,32" fill="none" stroke="var(--red)" stroke-width="2.5"/>
    <g fill="var(--red)"><circle cx="176" cy="133" r="5.5"/><circle cx="239" cy="114" r="5.5"/><circle cx="302" cy="93" r="5.5"/><circle cx="365" cy="72" r="5.5"/><circle cx="428" cy="52" r="5.5"/></g>
    <g fill="#fff" stroke="var(--grey)"><circle cx="50" cy="176" r="5.5"/><circle cx="113" cy="155" r="5.5"/><circle cx="491" cy="32" r="5.5"/></g>
    <text x="36" y="127" font-size="12" font-weight="700" fill="var(--ink)">INVESTISSEMENTS</text>
    <text x="310" y="128" font-size="12" font-weight="700" fill="var(--ink)">Espérance de gains</text>
    <text x="310" y="143" font-size="12" font-weight="700" fill="var(--ink)">pour l’investisseur</text>
    <g font-size="12" font-weight="700" fill="var(--ink)">
      <text x="36" y="198">2012</text><text x="96" y="198">2013</text><text x="158" y="198">2014</text>
      <text x="348" y="198">2017</text><text x="475" y="198">2019</text>
    </g>
    <g font-size="12" font-weight="700" fill="#fff">
      <rect x="491" y="10" width="239" height="34" fill="var(--sky)"/><text x="500" y="31">PLUS VALUES HOTELIÈRES</text>
      <rect x="491" y="51" width="239" height="33" fill="var(--blue)"/><text x="500" y="72">PLUS VALUES IMMOBILIÈRES</text>
      <rect x="491" y="90" width="239" height="34" fill="var(--navy)"/><text x="500" y="111">RENDEMENT ANNUEL CAPITALISÉ</text>
      <rect x="491" y="131" width="239" height="53" fill="var(--red-dark)"/><text x="500" y="152">REMBOURSEMNT</text><text x="500" y="167">DU CAPITAL INITIAL</text>
      <rect x="714" y="21" width="9" height="9"/><rect x="714" y="62" width="9" height="9"/><rect x="714" y="102" width="9" height="9"/><rect x="714" y="152" width="9" height="9"/>
    </g>
    <line x1="718" y1="184" x2="718" y2="220" stroke="var(--ink)" stroke-width="1"/>
    <text x="714" y="199" font-size="10" text-anchor="end" fill="#444">Exonération fiscale</text>
    <text x="714" y="213" font-size="10" text-anchor="end" fill="#444">(hors prélèvement sociaux)</text>
  </svg>

  <section class="block" style="top:698px">
    <h2 class="section-title">Comment sont répartis les gains ?</h2>
    <p style="margin-top:16px">Le capital de la société MORVANE CAPITAL est constitué de deux types de catégorie d’actions A et B.</p>
    <ul class="plain" style="margin-top:15px">
      <li>Les actions de type A destinées aux investisseurs.</li>
      <li>Les actions de type B (carried-interest) destinées à être souscrites par les personnes intervenant dans la gestion de MORVANE CAPITAL</li>
      <li>En vertu des dispositions légales et statutaires applicables, l’émission de 100 actions de type A oblige à émettre 1 action B Ne pouvant être souscrite que par les personnes intervenant dans la gestion de MORVANE CAPITAL.</li>
    </ul>
    <p>Les droits préférentiels attachés aux actions A et aux actions B sont définis à l’article 14.2 des statuts de Morvane Capital et répondent notamment au principe selon lequel l’actif net de liquidation au-delà d’un “rendement” de 7% l’an sera réparti à hauteur de 80% pour les actions A (investisseurs) et 20% pour les actions B (personnes intervenant dans la gestion du fonds).</p>
  </section>

  <svg class="share-chart" width="230" height="250" viewBox="0 0 230 250" font-family="Arimo, Arial, sans-serif" font-weight="700">
    <defs><radialGradient id="barGlow" cx="0.5" cy="0.45" r="0.6"><stop offset="0" stop-color="#d2282e"/><stop offset="1" stop-color="var(--red-dark)"/></radialGradient></defs>
    <text x="2" y="14" font-size="12" fill="var(--ink)">PARTAGE DE GAINS ESPÉRÉS</text>
    <rect x="0" y="29" width="107" height="144" fill="url(#barGlow)"/>
    <text x="53" y="57" font-size="22" fill="#fff" text-anchor="middle">80%</text>
    <rect x="116" y="139" width="106" height="34" fill="var(--red-dark)"/>
    <text x="169" y="162" font-size="18" fill="#fff" text-anchor="middle">20%</text>
    <rect x="0" y="176" width="107" height="31" fill="var(--grey)"/><text x="53" y="196" font-size="12.5" text-anchor="middle" fill="var(--ink)">Investisseur</text>
    <rect x="116" y="176" width="106" height="31" fill="var(--grey)"/><text x="169" y="196" font-size="12.5" text-anchor="middle" fill="var(--ink)">Gestionnaire</text>
    <rect x="0" y="211" width="107" height="32" fill="var(--black)"/><text x="53" y="232" font-size="12.5" text-anchor="middle" fill="#fff">Actions A</text>
    <rect x="116" y="211" width="106" height="32" fill="var(--black)"/><text x="169" y="232" font-size="12.5" text-anchor="middle" fill="#fff">Actions B</text>
  </svg>

  <div class="footer-rule"></div>
</main>
</body>
</html>
```